Professional looking Roller Blind Discount Card that portrays quality at a value for money price!

We need a double sided business card designed as a discount card. Size 90mm wide x 55mm high.We would like it to look professional and portray quality at a value for money price point.I have uploaded a word document with a basic layout with the information we want included on each side of the card. Please put your own thought into the layout.

Contact Information for Business Card

As per word document attached.

```html
<!DOCTYPE html>
<html lang="en">
<head>
<meta charset="utf-8">
<title>Roller Blinds Discount Card</title>
<link rel="stylesheet" href="https://fonts.googleapis.com/css2?family=Montserrat:wght@400;600;700&family=Oswald:wght@600&display=swap">
<style>
  :root {
    --blue: #2ea3df;
    --grey: #5e5e60;
    --white: #ffffff;
    --stage: #3a3a3c;
    --text-grey: #555557;
  }
  * { box-sizing: border-box; margin: 0; padding: 0; }
  html, body { width: 1200px; height: 896px; overflow: hidden; }
  body {
    background: var(--stage);
    font-family: "Montserrat", Arial, sans-serif;
    position: relative;
  }
  .card {
    position: absolute;
    top: 283px;
    width: 540px;
    height: 330px;
    background: var(--white);
    overflow: hidden;
    box-shadow: 0 6px 18px rgba(0,0,0,.35);
  }
  .card--front { left: 40px; }
  .card--back { left: 620px; }

  /* Front */
  .headline {
    position: absolute; left: 26px; top: 18px;
    font-family: "Oswald", Arial, sans-serif;
    font-weight: 600; font-size: 34px; letter-spacing: 1px;
    color: var(--blue); line-height: 1;
  }
  .offer-line {
    position: absolute; left: 26px; top: 62px;
    font-size: 20px; color: var(--text-grey); font-weight: 400;
  }
  .offer-line strong { color: var(--blue); font-weight: 700; }
  .photo {
    position: absolute; top: 100px; height: 108px;
  }
  .photo--window { left: 26px; width: 150px; background: linear-gradient(160deg, #b9b2aa, #7d8a6e 55%, #5c6b4d); }
  .photo--playroom { left: 180px; width: 150px; background: linear-gradient(135deg, #d9473f, #f0c93b 35%, #3fa2d8 65%, #55b447); }
  .front-brand {
    position: absolute; left: 26px; top: 224px;
    display: flex; align-items: center; gap: 12px;
    white-space: nowrap;
  }
  .front-brand .brand-mark { width: 36px; height: 36px; background: var(--blue); flex: none; }
  .front-brand .brand-name {
    font-size: 32px; font-weight: 600; color: var(--blue);
    letter-spacing: 1px; line-height: 1;
  }
  .call-band {
    position: absolute; left: 0; bottom: 0; width: 100%; height: 50px;
    background: var(--grey);
    display: flex; align-items: center; justify-content: flex-end;
    padding-right: 30px;
    font-size: 19px; font-weight: 700; color: var(--white);
  }
  .call-band .call-label { color: var(--blue); margin-right: 6px; }

  /* Back */
  .discount {
    position: absolute; left: 30px; top: 20px;
    font-family: "Oswald", Arial, sans-serif;
    font-weight: 600; font-size: 40px; color: var(--text-grey); line-height: 1;
  }
  .range-band {
    position: absolute; top: 78px; left: 0; width: 100%; height: 54px;
    display: flex;
  }
  .range-band .cap { width: 30px; background: var(--grey); }
  .range-band .cap--end { width: 170px; }
  .range-band .range-text {
    flex: 1; background: var(--blue); color: var(--white);
    font-size: 15px; line-height: 1.3; padding: 7px 14px;
    white-space: nowrap;
  }
  .back-brand {
    position: absolute; left: 30px; top: 164px; width: 270px;
    display: flex; align-items: center; gap: 12px;
  }
  .back-brand .brand-mark-small { width: 40px; height: 40px; background: var(--blue); flex: none; }
  .back-brand .brand-name-small { font-size: 21px; font-weight: 600; color: var(--blue); line-height: 1.15; }
  .divider {
    position: absolute; left: 320px; top: 150px; width: 1px; height: 110px;
    background: var(--blue);
  }
  .seal-placeholder {
    position: absolute; left: 380px; top: 150px;
    width: 100px; height: 100px; border-radius: 50%;
    background: var(--grey);
  }
  .footer-bands {
    position: absolute; left: 0; bottom: 0; width: 100%; height: 50px; display: flex;
  }
  .footer-bands .family {
    width: 270px; background: var(--blue); color: var(--white);
    font-size: 16px; font-weight: 700; display: flex; align-items: center;
    padding-left: 20px; white-space: nowrap;
  }
  .footer-bands .call {
    flex: 1; background: var(--grey); color: var(--white);
    font-size: 16px; font-weight: 700; display: flex; align-items: center; justify-content: center;
    white-space: nowrap;
  }
</style>
</head>
<body>
  <section class="card card--front">
    <h1 class="headline">ROLLER BLINDS</h1>
    <p class="offer-line"><strong>FREE</strong> in Home Measure &amp; Quote</p>
    <div class="photo photo--window" role="img" aria-label="Photo of a window fitted with a roller blind"></div>
    <div class="photo photo--playroom" role="img" aria-label="Photo of a bright playroom with coloured balls"></div>
    <div class="front-brand">
      <div class="brand-mark"></div>
      <p class="brand-name">BRAMWELL BLINDS CO</p>
    </div>
    <div class="call-band"><span class="call-label">Call</span> 0400 123 456 Today</div>
  </section>

  <section class="card card--back">
    <p class="discount">25% OFF</p>
    <div class="range-band">
      <div class="cap"></div>
      <p class="range-text">Quality Custom Made Roller Blinds<br>Blockout - Screen - Light Filtering</p>
      <div class="cap cap--end"></div>
    </div>
    <div class="back-brand">
      <div class="brand-mark-small"></div>
      <p class="brand-name-small">BRAMWELL<br>BLINDS CO</p>
    </div>
    <div class="divider"></div>
    <div class="seal-placeholder" role="img" aria-label="Price guarantee seal"></div>
    <div class="footer-bands">
      <div class="family">Family Owned &amp; Operated</div>
      <div class="call">Call 0400 123 456 Today!</div>
    </div>
  </section>
</body>
</html>
```